FunBrixo Business Card

We need a business card design for our company. We sell construction-themed amusement rides for kids.

Contact Information for Business Card

Contact info on business card should include:
Carl Dunning
Co-Founder & COO
(833) 571-FUNBRIX
Carl@funbrixo-demo.com
www.funbrixo-demo.com

```html
<!DOCTYPE html>
<html lang="en">
<head>
<meta charset="utf-8">
<title>FunBrixo Business Card</title>
<link href="https://fonts.googleapis.com/css2?family=Roboto:wght@400;700;900&display=swap" rel="stylesheet">
<style>
  :root {
    --backdrop: #2b2b2b;
    --card-white: #ffffff;
    --card-grey: #7b7c80;
    --brand-orange: #ec5a24;
    --text-dark: #222222;
    --rule-grey: #9a9a9a;
    --art-yellow: #e9b43a;
    --art-skin: #c9a48a;
    --art-blue: #3a5a8c;
  }
  * { margin: 0; padding: 0; box-sizing: border-box; }
  html, body { width: 1200px; height: 1200px; overflow: hidden; }
  body {
    background: var(--backdrop);
    font-family: "Roboto", Arial, sans-serif;
    position: relative;
  }
  .card {
    position: absolute;
    top: 310px;
    height: 594px;
  }
  .card-front { left: 234px; width: 364px; background: var(--card-white); }
  .card-back { left: 627px; width: 369px; background: var(--card-grey); }

  .brand {
    position: absolute;
    left: 0; right: 0;
    display: flex;
    align-items: center;
    justify-content: center;
    gap: 12px;
    font-weight: 900;
    font-size: 50px;
    letter-spacing: -1px;
  }
  .brand-dot { width: 22px; height: 22px; border-radius: 50%; }
  .card-front .brand { top: 425px; top: 425px; }
  .card-front .brand { top: 115px; color: var(--brand-orange); }
  .card-front .brand-dot { background: var(--brand-orange); }
  .card-back .brand { top: 115px; color: var(--card-white); }
  .card-back .brand-dot { background: var(--card-white); }

  .person { position: absolute; top: 340px; left: 0; right: 0; text-align: center; }
  .person-name { color: var(--brand-orange); font-weight: 700; font-size: 26px; line-height: 30px; }
  .person-title { color: var(--text-dark); font-size: 19px; line-height: 24px; }

  .contact-rule {
    position: absolute; top: 414px; left: 63px; right: 61px;
    display: flex; align-items: center; gap: 6px;
  }
  .contact-rule .line { flex: 1; height: 1px; background: var(--rule-grey); }
  .contact-rule .icons { display: flex; gap: 6px; padding: 0 6px; }
  .icon-tile {
    width: 32px; height: 32px; background: var(--brand-orange); border-radius: 3px;
    display: flex; align-items: center; justify-content: center;
  }

  .contact-list { position: absolute; top: 461px; left: 0; right: 0; text-align: center; list-style: none; }
  .contact-list li { color: var(--text-dark); font-size: 19px; line-height: 27px; }
  .contact-list .accent { color: var(--brand-orange); }

  .crew-art {
    position: absolute; left: 30px; top: 270px; width: 310px; height: 310px;
    background: linear-gradient(180deg, var(--art-yellow) 0%, var(--art-skin) 38%, var(--art-blue) 100%);
    opacity: 0.85;
    border-radius: 8px;
  }
</style>
</head>
<body>
  <section class="card card-front">
    <div class="brand"><span class="brand-dot"></span>FunBrixo</div>

    <div class="person">
      <p class="person-name">CARL DUNNING</p>
      <p class="person-title">Co-Founder &amp; COO</p>
    </div>

    <div class="contact-rule">
      <span class="line"></span>
      <div class="icons">
        <span class="icon-tile">
          <svg width="20" height="20" viewBox="0 0 20 20" fill="none" stroke="#fff" stroke-width="1.6">
            <path d="M3 8c0-3 3-4 7-4s7 1 7 4l-3 1-1-2H7L6 9z" fill="#fff"/>
            <rect x="4" y="10" width="12" height="7" rx="1"/>
          </svg>
        </span>
        <span class="icon-tile">
          <svg width="20" height="20" viewBox="0 0 20 20" fill="none" stroke="#fff" stroke-width="1.6">
            <rect x="2.5" y="5" width="15" height="10" rx="1"/>
            <path d="M3 6l7 5 7-5"/>
          </svg>
        </span>
        <span class="icon-tile">
          <svg width="20" height="20" viewBox="0 0 20 20" fill="none" stroke="#fff" stroke-width="1.6">
            <circle cx="10" cy="10" r="7"/>
            <path d="M3 10h14M10 3c-3 4-3 10 0 14M10 3c3 4 3 10 0 14"/>
          </svg>
        </span>
      </div>
      <span class="line"></span>
    </div>

    <ul class="contact-list">
      <li>(833) 571-FUNBRIX</li>
      <li>Carl@funbrixo-demo.com</li>
      <li>www.<span class="accent">funbrixo-demo</span>.com</li>
    </ul>
  </section>

  <section class="card card-back">
    <div class="brand"><span class="brand-dot"></span>FunBrixo</div>
    <div class="crew-art" role="img" aria-label="Illustration of two cartoon construction workers in yellow hard hats, arms crossed"></div>
  </section>
</body>
</html>
```